Velvet Table

A quick run down of the iPhone app and what it does:

1. It has a home screen for that restaurant that will guide you to the menu.
2. You can search the menu which has all the pictures of the items on the menu.
3. There are also ratings from the users on each item.
4. You can also order and pay from the app.

Please see this link to look at the wire-frame we have created (Click on the buttons to move from page to page)
https://www.plandraft.example/editor/live/preview/p_4KdmTrwQzLpxeNvBcHyUaJ2PQ8xwrt5m.2738491026374

We would like something that is very clean, minimalist and uses modern design to convey the feeling of cultured.

I would like the designer to create at least 5 pages:

1. The Home screen to the restaurant. (call it Harbor Plate) You can redo the buttons to make it look better. Like have a logo or something better than box buttons. Please use good looking easy to read fonts, Modern you might say.

2. and 3. The Menu page with 3 items and pictures per menu title like Appetizers and Entrees have it look as if it is dropping down (you can use your own photos or some from the web with descriptions like what you see on the Wire-frame)

4. The item drill down, as you click on an item from the menu it comes up with a larger photo of the item and the description and also the rating under the description. (see wire-frame)

5. The order page with items from the menu on the order page with prices.

I would like for the bottom menu to be updated with some nice looking buttons. For one the help now button I would like to have a circle with an outline of a person raising their hand.

I currently don't have a logo or photos so I will rely on your discretion to find the photos you need. I also have no particular colors in mind but here are some app designs I really like.

http://gallery-mocks.example/tagged/app_velo#show-all

http://31.media.picshelf.example/4a9c27e0b3d15f86ac024e7b91d3f6c2/pics_k4tzbqweLM2s83kpq2_400.png (put the item name on this and a plus sign in the top right of the photo)

http://37.media.picshelf.example/b71e05ac9d24f3e8c6a1570d2fe9b8c4/pics_k4tz7rvhQW9s83kpq2_400.png ( take out all the words and put in all the information I have on the page with the large picture, from my wire-frame, the drill down page)

If you follow the same sort of app design with a photo in the background of the restaurant home page and clear design like this you will for sure win.

Also after this is done I will most likely have the winning designer create my logo, and app icon.

Target Market(s)

The target market of this App are people that can afford to eat out and enjoy using technology to have a better dining experience. Ages 16 to 45 Male and Female.

Industry/Entity Type

Restaurant

Font styles to use
Sans Serif

Requirements
Must have
• Clear, high quality photos, I don't want to see any individual pixels. Please read my outline carefully to understand what this app will do.
Nice to have
• I want to feel like I'm having a good experience from the moment I open the app the the moment I finish my meal with the app. Come up with something simple and creative for the user to experience while dining.
Should not have
• Please do not just submit my wire-frame in different colors that will be a waste of your time and mine. I don't want to see boxes as the buttons.

```html
<!DOCTYPE html>
<html lang="en">
<head>
<meta charset="utf-8">
<title>Harbor Plate – App Screens</title>
<link href="https://fonts.googleapis.com/css2?family=Open+Sans:wght@400;600;700&display=swap" rel="stylesheet">
<style>
:root{
  --stage:#d8d5d0;
  --screen:#1b1b1b;
  --bar:#0d0d0d;
  --band:rgba(20,20,20,.82);
  --white:#ffffff;
  --muted:#bdbdbd;
  --star:#4a8ac9;
  --accent:#3f8fd4;
  --button:#4877a6;
  --chip:#2e2e2e;
}
*{box-sizing:border-box;margin:0;padding:0}
html,body{width:1200px;height:589px;overflow:hidden}
body{background:var(--stage);font-family:'Open Sans',Arial,sans-serif;color:var(--white);position:relative}
.screen{position:absolute;top:78px;width:255px;height:434px;background:var(--screen);overflow:hidden;box-shadow:0 6px 18px rgba(0,0,0,.25)}
.screen--home{left:33px}
.screen--menu{left:329px}
.screen--item{left:628px}
.screen--order{left:921px}
.abs{position:absolute}

/* bottom nav */
.tabbar{position:absolute;left:0;right:0;bottom:0;height:39px;background:var(--bar);display:flex;justify-content:space-around;align-items:center}
.tab{display:flex;flex-direction:column;align-items:center;width:60px}
.tab svg{width:22px;height:22px}
.tab span{font-size:5px;font-weight:700;text-transform:uppercase;margin-top:1px;letter-spacing:.2px}
.tabbar--wide .tab span{text-transform:none;font-size:5.5px}
.tabbar--split .tab{width:50%;border-right:1px solid #333}
.tabbar--split .tab:last-child{border-right:0}

/* home */
.home-photo{position:absolute;inset:0;background:
  radial-gradient(ellipse at 45% 48%,#f0b070 0%,#b9642a 22%,#4a2a1a 50%,#1f1814 80%),#1f1814}
.search{position:absolute;left:10px;top:9px;width:236px;height:20px;border-radius:10px;background:rgba(90,80,75,.6)}
.search svg{position:absolute;top:3px}
.category{position:absolute;width:92px;height:92px;border-radius:50%;background:rgba(130,110,100,.35);display:flex;flex-direction:column;align-items:center;justify-content:center;text-align:center}
.category svg{width:42px;height:42px;margin-bottom:4px}
.category span{font-size:9px;font-weight:700;text-transform:uppercase}
.dot{position:absolute;border-radius:50%}

/* menu list */
.topbar{position:absolute;left:0;right:0;top:0;height:39px;background:var(--bar);font-size:10px}
.topbar .back{position:absolute;left:5px;top:13px}
.topbar .title{position:absolute;left:0;right:0;top:13px;text-align:center}
.dish-photo{position:absolute;left:0;right:0}
.plus{position:absolute;width:22px;height:22px;border:1.5px solid var(--white);border-radius:50%;display:flex;align-items:center;justify-content:center;font-size:17px;line-height:1;font-weight:400}
.dish-band{position:absolute;left:0;right:0;background:var(--band)}
.dish-name{position:absolute;left:7px;font-size:14px}
.dish-price{position:absolute;right:11px;font-size:13px;font-weight:600}
.rating{position:absolute;font-size:6.5px;color:var(--muted);display:flex;align-items:center;gap:3px}
.stars{color:var(--star);font-size:11px;letter-spacing:.5px}
.stars .off{color:#666}
.stars .lite{color:var(--white)}

/* item */
.item-caption{position:absolute;left:0;right:0;top:118px;height:53px;background:var(--band)}
.item-desc{position:absolute;left:13px;right:4px;top:144px;font-size:8.6px;line-height:11px}
.reviews-head{position:absolute;left:0;right:0;top:183px;font-size:8px;font-weight:700;text-align:center}
.reviews-count{position:absolute;right:13px;top:183px;font-size:8px;color:var(--accent);font-weight:600}
.review{position:absolute;left:12px;right:14px;font-size:8.6px;line-height:10.5px}
.review .who{font-weight:700;font-size:8.6px}
.review .rate{position:absolute;right:0;top:-2px;font-size:6.5px;display:flex;align-items:center;gap:3px}
.review .quote{text-align:center;font-weight:700;margin-top:3px}
.review p{text-align:center}

/* order */
.line{position:absolute;left:9px;right:11px;height:26px}
.line .name{font-size:13px;font-weight:700;position:absolute;left:0;top:0}
.qty{position:absolute;right:0;top:0;display:flex;align-items:center;gap:3px}
.qty .ctl{width:17px;height:17px;border:1.3px solid var(--white);border-radius:50%;display:flex;align-items:center;justify-content:center;font-size:13px;line-height:1}
.qty .num{width:26px;height:17px;background:var(--chip);border-radius:3px;text-align:center;font-size:11px;font-weight:600;line-height:17px}
.line .unit{position:absolute;right:22px;top:19px;font-size:8px;color:var(--muted);width:30px;text-align:center}
.subtotal{position:absolute;top:197px;font-size:13px;font-weight:700}
.submit{position:absolute;left:24px;top:345px;width:194px;height:33px;background:var(--button);border-radius:3px;font-size:10.5px;font-weight:600;display:flex;align-items:center;justify-content:center}
.order-bg{position:absolute;inset:0;background:radial-gradient(ellipse at 50% 30%,#2a2a2a,#161616 70%)}
</style>
</head>
<body>

<!-- Home -->
<section class="screen screen--home">
  <div class="home-photo" role="img" aria-label="Softly blurred photo of a warmly lit restaurant interior"></div>
  <div class="search">
    <svg style="left:4px" width="14" height="14" viewBox="0 0 14 14"><circle cx="6" cy="6" r="4.5" fill="none" stroke="#fff" stroke-width="1.4"/><line x1="9.3" y1="9.3" x2="13" y2="13" stroke="#fff" stroke-width="1.4"/></svg>
    <svg style="right:4px" width="14" height="14" viewBox="0 0 14 14"><circle cx="7" cy="7" r="5.5" fill="none" stroke="#aaa" stroke-width="1"/><path d="M5 5l4 4M9 5l-4 4" stroke="#aaa" stroke-width="1"/></svg>
  </div>

  <div class="category" style="left:10px;top:42px">
    <svg viewBox="0 0 42 42" fill="none" stroke="#fff" stroke-width="2"><path d="M8 14h13l-2 24H10z"/><path d="M21 20h13l-2 18H23"/><line x1="14" y1="14" x2="20" y2="3"/><circle cx="11" cy="11" r="3"/><line x1="28" y1="20" x2="31" y2="10"/></svg>
    <span>Drinks</span>
  </div>
  <div class="category" style="left:144px;top:42px">
    <svg viewBox="0 0 42 42" fill="#fff"><line x1="4" y1="38" x2="38" y2="4" stroke="#fff" stroke-width="2"/><rect x="10" y="24" width="8" height="8" rx="2" transform="rotate(-45 14 28)"/><circle cx="21" cy="21" r="4"/><rect x="24" y="10" width="8" height="8" rx="2" transform="rotate(-45 28 14)"/></svg>
    <span>Appetizers</span>
  </div>
  <div class="category" style="left:10px;top:145px">
    <svg viewBox="0 0 42 42" fill="#fff"><rect x="7" y="10" width="12" height="20" rx="1"/><line x1="14" y1="10" x2="17" y2="3" stroke="#fff" stroke-width="2"/><rect x="16" y="22" width="22" height="5" rx="2.5"/><rect x="14" y="28" width="26" height="4" rx="2"/><rect x="16" y="33" width="22" height="4" rx="2"/></svg>
    <span>Entrees</span>
  </div>
  <div class="category" style="left:144px;top:145px">
    <svg viewBox="0 0 42 42" fill="#fff"><path d="M13 14a5 5 0 0 1 3-9 6 6 0 0 1 10 0 5 5 0 0 1 3 9v3H13z"/><rect x="10" y="28" width="22" height="12" rx="2"/><rect x="14" y="19" width="14" height="7" rx="2"/></svg>
    <span>Chef's Choice</span>
  </div>
  <div class="category" style="left:10px;top:244px">
    <svg viewBox="0 0 42 42" fill="none" stroke="#fff" stroke-width="2"><rect x="6" y="16" width="30" height="20"/><path d="M6 24c5-4 8 4 15 0s10 4 15 0"/><path d="M6 16l15-8 15 8"/></svg>
    <span>Desserts</span>
  </div>
  <div class="category" style="left:144px;top:244px">
    <svg viewBox="0 0 42 42" fill="none" stroke="#fff" stroke-width="2"><path d="M6 16l3-8h24l3 8"/><path d="M6 16c0 3 5 3 6 0 1 3 5 3 6 0 1 3 5 3 6 0 1 3 5 3 6 0 1 3 6 3 6 0"/><path d="M9 20v16h24V20"/><rect x="17" y="26" width="8" height="10"/></svg>
    <span>Others</span>
  </div>

  <div class="dot" style="left:113px;top:328px;width:14px;height:14px;background:rgba(200,200,200,.7)"></div>
  <div class="dot" style="left:87px;top:360px;width:14px;height:14px;background:rgba(200,200,200,.6)"></div>
  <div class="dot" style="left:108px;top:352px;width:30px;height:30px;background:var(--accent)"></div>
  <div class="dot" style="left:146px;top:360px;width:14px;height:14px;background:rgba(200,200,200,.6)"></div>

  <nav class="tabbar">
    <div class="tab"><svg viewBox="0 0 22 22" fill="none" stroke="#fff" stroke-width="1.3"><circle cx="11" cy="11" r="10"/><path d="M5 14h12M6 14a5 5 0 0 1 10 0"/></svg><span>Order</span></div>
    <div class="tab"><svg viewBox="0 0 22 22" fill="none" stroke="#fff" stroke-width="1.3"><circle cx="11" cy="11" r="10"/><path d="M8.5 8.5a2.5 2.5 0 1 1 3.5 2.3c-.7.4-1 .9-1 1.7v.8"/><circle cx="11" cy="16" r=".6" fill="#fff"/></svg><span>Help Now</span></div>
    <div class="tab"><svg viewBox="0 0 22 22" fill="none" stroke="#fff" stroke-width="1.3"><circle cx="11" cy="11" r="10"/><path d="M7 5v12M5 5v3a2 2 0 0 0 4 0V5M14 5c2 0 3 2 3 5h-3v7"/></svg><span># Table</span></div>
    <div class="tab"><svg viewBox="0 0 22 22" fill="none" stroke="#fff" stroke-width="1.3"><circle cx="11" cy="11" r="10"/><path d="M6 8h10M6 11h10M6 14h10"/></svg><span>Menu</span></div>
  </nav>
</section>

<!-- Menu list -->
<section class="screen screen--menu">
  <header class="topbar"><span class="back">&lt; Back</span><span class="title">Appetizers</span></header>

  <div class="dish-photo" style="top:39px;height:155px;background:linear-gradient(160deg,#cfd6d0 0%,#8f9d8d 40%,#5f8f4a 70%,#2d3a2a 100%)" role="img" aria-label="Cucumber cups topped with goat cheese and tomato"></div>
  <div class="plus" style="right:8px;top:49px">+</div>
  <div class="dish-band" style="top:155px;height:44px"></div>
  <div class="dish-name" style="top:158px">Cucumber Cup</div>
  <div class="dish-price" style="top:158px">$10</div>
  <div class="rating" style="left:12px;top:178px">Rating <span class="stars">★★★★<span class="off">★</span></span></div>

  <div class="dish-photo" style="top:199px;height:160px;background:radial-gradient(ellipse at 45% 45%,#e8574f 0%,#c92f34 45%,#6a1f22 80%,#2a2222 100%)" role="img" aria-label="Watermelon cubes topped with whipped cheese and herbs"></div>
  <div class="plus" style="right:8px;top:208px">+</div>
  <div class="dish-band" style="top:329px;height:66px"></div>
  <div class="dish-name" style="top:331px">Watermelon Cup</div>
  <div class="dish-price" style="top:331px">$8</div>
  <div class="rating" style="left:12px;top:351px">Rating <span class="stars">★★★</span></div>

  <nav class="tabbar">
    <div class="tab"><svg viewBox="0 0 22 22" fill="none" stroke="#fff" stroke-width="1.3"><circle cx="11" cy="11" r="10"/><path d="M5 14h12M6 14a5 5 0 0 1 10 0"/></svg><span>Order</span></div>
    <div class="tab"><svg viewBox="0 0 22 22" fill="none" stroke="#fff" stroke-width="1.3"><circle cx="11" cy="11" r="10"/><path d="M8 14l5-6M13 8l1-3"/><circle cx="10" cy="16" r="1.5"/></svg><span>Help Now</span></div>
    <div class="tab"><svg viewBox="0 0 22 22" fill="none" stroke="#fff" stroke-width="1.3"><circle cx="11" cy="11" r="10"/><path d="M7 5v12M5 5v3a2 2 0 0 0 4 0V5M14 5c2 0 3 2 3 5h-3v7"/></svg><span># Table</span></div>
    <div class="tab"><svg viewBox="0 0 22 22" fill="none" stroke="#fff" stroke-width="1.3"><circle cx="11" cy="11" r="10"/><path d="M6 8h10M6 11h10M6 14h10"/></svg><span>Menu</span></div>
  </nav>
</section>

<!-- Item detail -->
<section class="screen screen--item">
  <div class="dish-photo" style="top:0;height:171px;background:linear-gradient(160deg,#d6ddd6 0%,#9aa79a 35%,#5f8f4a 65%,#2d3a2a 100%)" role="img" aria-label="Close-up of herbed goat cheese cucumber party bites"></div>
  <div class="plus" style="right:10px;top:8px">+</div>
  <div class="item-caption"></div>
  <div class="dish-name" style="left:16px;top:121px">Cucumber Cup</div>
  <div class="rating" style="left:156px;top:125px">Rating <span class="stars">★★★<span class="off">★</span></span></div>
  <p class="item-desc">Refreshing combination of Cucumber and goat cheese in Herbed Goat Cheese-Cucumber Party Bites.</p>

  <div class="reviews-head">Reviews</div>
  <div class="reviews-count">23</div>

  <article class="review" style="top:214px">
    <div class="who">Owen Hartley</div>
    <div class="rate">Rating <span class="stars">★★★★★</span></div>
    <div class="quote">“Very cool spot with great appetizers!”</div>
    <p>We found this place upon recommendation of restaurant close by. We sat at the bar, had a few drinks, some appetizers &amp; enjoyed chatting with the owner. Really enjoyed.</p>
  </article>
  <article class="review" style="top:304px">
    <div class="who">Ravi</div>
    <div class="rate">Rating <span class="stars">★★★★<span class="lite">★</span></span></div>
    <div class="quote">“Great evening of wine tasting”</div>
    <p>Five friends enjoyed a great evening of wine tasting, we also came back rather late the following evening</p>
  </article>
  <article class="review" style="top:365px">
    <div class="who">Lucas</div>
    <div class="quote">“Watermelon cup”</div>
  </article>

  <nav class="tabbar tabbar--wide tabbar--split">
    <div class="tab"><svg viewBox="0 0 22 22" fill="none" stroke="#fff" stroke-width="1.3" style="width:28px;height:28px"><circle cx="11" cy="11" r="10"/><path d="M9 17v-5l-2-5M9 12h4l2-6"/><circle cx="15.5" cy="5" r="1" fill="#fff"/></svg><span>Help Now</span></div>
    <div class="tab"><svg viewBox="0 0 22 22" fill="none" stroke="#fff" stroke-width="1.3" style="width:28px;height:28px"><circle cx="11" cy="11" r="10"/><path d="M5 14h12M6 14a5 5 0 0 1 10 0M11 9V8"/></svg><span>Order</span></div>
  </nav>
</section>

<!-- Order -->
<section class="screen screen--order">
  <div class="order-bg"></div>

  <div class="line" style="top:17px"><span class="name">Cucumber Cup</span><div class="qty"><span class="ctl">+</span><span class="num">2</span><span class="ctl">−</span></div><span class="unit">$10</span></div>
  <div class="line" style="top:63px"><span class="name">Cherry Fizz</span><div class="qty"><span class="ctl">+</span><span class="num">2</span><span class="ctl">−</span></div><span class="unit">$5</span></div>
  <div class="line" style="top:106px"><span class="name">Lime Spark</span><div class="qty"><span class="ctl">+</span><span class="num">1</span><span class="ctl">−</span></div><span class="unit">$3</span></div>
  <div class="line" style="top:153px"><span class="name">Cheese Burger</span><div class="qty"><span class="ctl">+</span><span class="num">1</span><span class="ctl">−</span></div><span class="unit">$1</span></div>

  <div class="subtotal" style="left:110px">Sub Total</div>
  <div class="subtotal" style="left:193px">$38</div>

  <div class="submit">Submit Order</div>

  <nav class="tabbar tabbar--wide">
    <div class="tab"><svg viewBox="0 0 22 22" fill="none" stroke="#fff" stroke-width="1.3" style="width:28px;height:28px"><circle cx="11" cy="11" r="10"/><path d="M7 15l1-3 6-6 2 2-6 6z"/></svg><span>Review</span></div>
    <div class="tab"><svg viewBox="0 0 22 22" fill="none" stroke="#fff" stroke-width="1.3" style="width:28px;height:28px"><circle cx="11" cy="11" r="10"/><path d="M8 17v-5l-2-5M8 12h3M12 15l5-5 1 1-5 5z"/></svg><span>Note for Waiter</span></div>
    <div class="tab"><svg viewBox="0 0 22 22" fill="none" stroke="#fff" stroke-width="1.3" style="width:28px;height:28px"><circle cx="11" cy="11" r="10"/><path d="M13.5 8c-.5-1-1.4-1.5-2.5-1.5-1.5 0-2.5.8-2.5 2s1 1.7 2.5 2 2.5.8 2.5 2-1 2-2.5 2c-1.2 0-2.1-.5-2.6-1.5M11 5v12"/></svg><span>Pay Now</span></div>
  </nav>
</section>

</body>
</html>
```